Business Card Design for company

We want new business cards. We'd like something different-- yet still highly professional. Our tagline is Providing leadership, delivering success. Stock photos are ok, as long as they are relevant and look upscale.

Target Market(s)

Architecture/Business Management Consulting/Engineering Consulting

Contact Information for Business Card

dark gray background with pops of blue might be good, but you tell me. You're the designers. Rounded corners might be nice, but again, you tell me.

Font styles to use
Serif
Sans Serif

Colors
3276b5
5c5c5c
9d9d9d
fbfbfb

Requirements
Nice to have
• Something different, but still very professional.

```html
<!DOCTYPE html>
<html lang="en">
<head>
<meta charset="utf-8">
<title>Arvel Group – Business Card</title>
<link href="https://fonts.googleapis.com/css2?family=Montserrat:wght@500;600;700&family=Open+Sans:wght@400&display=swap" rel="stylesheet">
<style>
  :root {
    --backdrop: #5c5c5c;
    --card-light: #f3f3f3;
    --card-dark: #2d2d2d;
    --brand-blue: #3276b5;
    --ink-dark: #3a3e44;
    --ink-body: #2b2b2b;
    --ink-white: #fbfbfb;
  }
  * { margin: 0; padding: 0; box-sizing: border-box; }
  html, body {
    width: 1200px;
    height: 900px;
    overflow: hidden;
    background: var(--backdrop);
  }
  .canvas {
    position: relative;
    width: 1200px;
    height: 900px;
  }
  .card {
    position: absolute;
    top: 200px;
    width: 310px;
    height: 502px;
  }
  .card--front {
    left: 253px;
    background: var(--card-light);
    border-radius: 52px 0 52px 0;
  }
  .card--back {
    left: 627px;
    background: var(--card-dark);
    border-radius: 0 52px 0 52px;
  }
  .brand-name {
    position: absolute;
    left: 0;
    width: 100%;
    text-align: center;
    font-family: "Montserrat", sans-serif;
    font-weight: 700;
    font-size: 34px;
    letter-spacing: 1px;
    color: var(--brand-blue);
  }
  .card--front .brand-name { top: 335px; top: 130px; }
  .card--back .brand-name { top: 220px; }

  .contact {
    position: absolute;
    left: 31px;
    top: 303px;
    font-family: "Open Sans", sans-serif;
    color: var(--ink-body);
  }
  .contact__name {
    font-family: "Montserrat", sans-serif;
    font-weight: 600;
    font-size: 17px;
    color: var(--ink-dark);
    line-height: 22px;
  }
  .contact__name .first { color: var(--brand-blue); }
  .contact__role {
    font-size: 14.5px;
    line-height: 20px;
    margin-bottom: 4px;
  }
  .contact__list { list-style: none; }
  .contact__list li {
    display: flex;
    align-items: center;
    gap: 7px;
    font-size: 14.5px;
    line-height: 18.5px;
  }
  .contact__list svg { width: 11px; height: 11px; fill: var(--brand-blue); flex: none; }
  .contact__address {
    margin-top: 5px;
    font-size: 14.5px;
    line-height: 18.5px;
  }
  .tagline {
    position: absolute;
    left: 0;
    top: 418px;
    width: 100%;
    text-align: center;
    font-family: "Montserrat", sans-serif;
    font-weight: 600;
    font-size: 16px;
    line-height: 21px;
    color: var(--ink-white);
    text-transform: uppercase;
  }
</style>
</head>
<body>
<main class="canvas">
  <section class="card card--front">
    <div class="brand-name">ARVEL GROUP</div>
    <div class="contact">
      <p class="contact__name"><span class="first">DANIEL</span> HART</p>
      <p class="contact__role">Managing Director</p>
      <ul class="contact__list">
        <li><svg viewBox="0 0 12 12" aria-hidden="true"><path d="M1 3.5C1 2 2.5 1.5 6 1.5S11 2 11 3.5V5H8.5V4h-5v1H1zM3 5.5h6l1.5 5h-9z"/></svg>044-555 210 348</li>
        <li><svg viewBox="0 0 12 12" aria-hidden="true"><path d="M3.5 0.5h5a1 1 0 0 1 1 1v9a1 1 0 0 1-1 1h-5a1 1 0 0 1-1-1v-9a1 1 0 0 1 1-1zM4 2v7h4V2z"/></svg>044-555 210 349</li>
        <li><svg viewBox="0 0 12 12" aria-hidden="true"><path d="M0.5 2.5h11v7h-11zM1.5 3.3L6 6.5l4.5-3.2v-.3h-9z"/></svg>info@arvelgroup.com</li>
        <li><svg viewBox="0 0 12 12" aria-hidden="true"><circle cx="6" cy="6" r="5.5"/></svg>www.arvelgroup.com</li>
      </ul>
      <p class="contact__address">12345, Address Goes Here<br>Country Name, 123456.</p>
    </div>
  </section>

  <section class="card card--back">
    <div class="brand-name">ARVEL GROUP</div>
    <p class="tagline">Providing Leadership<br>Delivering Success</p>
  </section>
</main>
</body>
</html>
```